Heritage Hollow Business Cards

Require a business card design. <br/><br/>Needs to include logo (either round or long version) plus these details:<br/>Maya Torvell<br/>Heritage Hollow<br/>maya@kelvadtrading.com.au<br/>02 6481 7395<br/>PO Box Glenwarra NSW 2791<br/>www.heritagehollow.com.au<br/><br/>I need in an editable format so that I can create for multiple staff members. <br/><br/>

Target Market(s)

We are an online store selling renovation products to home owners are builders. Looking for a classic classy design.

Industry/Entity Type

Home And Garden

Contact Information for Business Card

Maya Torvell
Heritage Hollow
maya@kelvadtrading.com.au
02 6481 7395
PO Box Glenwarra NSW 2791
www.heritagehollow.com.au

Colors

Designer to choose colors to be used in the design.

Requirements
Must have
• Must include Logo.

```html
<!DOCTYPE html>
<html lang="en">
<head>
<meta charset="utf-8">
<title>Heritage Hollow Business Cards</title>
<link href="https://fonts.googleapis.com/css2?family=Work+Sans:wght@400;600&display=swap" rel="stylesheet">
<style>
  :root {
    --page: #141414;
    --card-dark: #1c1c1c;
    --card-light: #2c2c2c;
    --ink: #f2f2f2;
    --ink-muted: #8c8c8c;
    --rule: #9a9a9a;
  }
  * { margin: 0; padding: 0; box-sizing: border-box; }
  html, body {
    width: 1200px; height: 900px; overflow: hidden;
    background: var(--page);
    font-family: "Work Sans", Arial, sans-serif;
    color: var(--ink);
  }
  .sheet {
    width: 1200px; height: 900px;
    display: flex; flex-direction: column; align-items: center; justify-content: center;
    gap: 40px;
  }
  .card {
    width: 700px; height: 400px;
    background: linear-gradient(125deg, var(--card-dark) 0%, var(--card-dark) 45%, var(--card-light) 80%, var(--card-dark) 100%);
    position: relative;
    box-shadow: 0 14px 30px rgba(0,0,0,0.6);
  }
  .brand-mark {
    border: 1.5px solid var(--ink);
    border-radius: 50%;
    display: flex; align-items: center; justify-content: center;
    text-align: center;
  }
  .brand-name {
    font-weight: 600;
    color: var(--ink);
    line-height: 1.05;
  }
  /* Front */
  .card-front .brand-mark {
    position: absolute; left: 50%; top: 50px;
    width: 230px; height: 230px; margin-left: -115px;
  }
  .card-front .brand-name { font-size: 34px; }
  .card-front .website {
    position: absolute; left: 0; right: 0; bottom: 62px;
    text-align: center; font-size: 17px; letter-spacing: 4px;
  }
  /* Back */
  .card-back .brand-mark {
    position: absolute; left: 70px; top: 95px;
    width: 210px; height: 210px;
  }
  .card-back .brand-name { font-size: 31px; }
  .divider {
    position: absolute; left: 330px; top: 75px;
    width: 1.5px; height: 250px; background: var(--rule);
  }
  .contact {
    position: absolute; left: 365px; top: 75px;
  }
  .person-name { font-size: 32px; font-weight: 600; letter-spacing: 1.5px; }
  .person-role { font-size: 17px; margin-top: 2px; }
  .company { font-size: 18px; color: var(--ink-muted); margin-top: 16px; }
  .address { font-size: 19px; letter-spacing: 1px; line-height: 1.3; margin-top: 8px; }
  .contact-list { list-style: none; margin-top: 12px; }
  .contact-list li {
    display: flex; align-items: center; gap: 12px;
    font-size: 19px; letter-spacing: 0.5px; line-height: 1.4;
  }
  .contact-list svg { width: 14px; height: 14px; flex: none; }
  .muted { color: var(--ink-muted); }
</style>
</head>
<body>
<main class="sheet">
  <section class="card card-front" aria-label="Card front">
    <div class="brand-mark"><span class="brand-name">Heritage<br>Hollow</span></div>
    <p class="website">www.heritagehollow.com.au</p>
  </section>

  <section class="card card-back" aria-label="Card back">
    <div class="brand-mark"><span class="brand-name">Heritage<br>Hollow</span></div>
    <div class="divider"></div>
    <div class="contact">
      <h1 class="person-name">Maya Torvell</h1>
      <p class="person-role">Director</p>
      <p class="company">Heritage Hollow</p>
      <p class="address">PO Box Glenwarra<br>NSW 2791</p>
      <ul class="contact-list">
        <li>
          <svg viewBox="0 0 14 14" aria-hidden="true"><path d="M3 1 L5 1 L6 4 L4.5 5.5 Q6 8.5 8.5 9.5 L10 8 L13 9 L13 11 Q12 13 10 13 Q2 11 1 3 Q1 1 3 1 Z" fill="none" stroke="#bbb" stroke-width="1.2"/></svg>
          02 6481 7395
        </li>
        <li>
          <svg viewBox="0 0 14 14" aria-hidden="true"><rect x="1" y="3" width="12" height="8" fill="none" stroke="#bbb" stroke-width="1.2"/><path d="M1 3 L7 8 L13 3" fill="none" stroke="#bbb" stroke-width="1.2"/></svg>
          maya@kelvadtrading.com.au
        </li>
        <li>
          <svg viewBox="0 0 14 14" aria-hidden="true"><circle cx="7" cy="7" r="6" fill="none" stroke="#bbb" stroke-width="1.2"/><ellipse cx="7" cy="7" rx="2.6" ry="6" fill="none" stroke="#bbb" stroke-width="1"/><path d="M1 7 H13" stroke="#bbb" stroke-width="1"/></svg>
          <span>www.<span class="muted">heritagehollow</span>.com.au</span>
        </li>
      </ul>
    </div>
  </section>
</main>
</body>
</html>
```